Website Design - TallyPorchHelpers.net

PLEASE CHECK WORD DOCUMENT ATTACHED FOR WEBSITE FLOW.

Target Market(s)

REAL ESTATE AGENTS ARE THE TARGET MARKET

Industry/Entity Type

Real Estate

Coding

Coded - Design and coding required

Number of Pages Required

4 page

Colors

Designer to choose colors to be used in the design.

Requirements
Must have
• WE LIKE RED LOGO ATTACHED
Nice to have
• PLEASE CHECK WORD DOCUMENT ATTACHED FOR WEBSITE FLOW.
Should not have

```html
<!DOCTYPE html>
<html lang="en">
<head>
<meta charset="utf-8">
<title>Tally Porch Helpers</title>
<link href="https://fonts.googleapis.com/css2?family=Montserrat:wght@300;400;600;700&family=Roboto:ital,wght@0,400;0,500;0,700;1,500&display=swap" rel="stylesheet">
<style>
:root{
  --red:#e3051b;
  --navy:#211e7a;
  --ink:#1d1d1d;
  --grey:#6b6b6b;
  --light:#9a9a9a;
  --paper:#ffffff;
  --mist:#efeded;
  --card-head:#e9e9e9;
  --footer:#1c1c1c;
}
*{margin:0;padding:0;box-sizing:border-box}
html,body{width:1200px;height:2857px;overflow:hidden;background:var(--paper)}
body{position:relative;font-family:"Roboto",Arial,sans-serif;color:var(--ink)}
.abs{position:absolute}
.top-rule{left:0;top:0;width:1200px;height:6px;background:var(--red)}
.header{left:0;top:6px;width:1200px;height:104px;background:var(--paper)}
.brand{left:100px;top:36px;display:flex;align-items:center;gap:10px;font-family:"Montserrat",sans-serif;font-weight:700;font-size:19px;line-height:20px;color:var(--navy)}
.brand-mark{width:30px;height:30px;border:3px solid var(--navy)}
.nav a{position:absolute;top:50px;font-size:15px;color:#333;text-decoration:none}
.phone-circle{left:873px;top:40px;width:38px;height:38px;border:1px solid #bbb;border-radius:50%;display:flex;align-items:center;justify-content:center}
.call{left:922px;top:49px;font-size:16px;font-weight:500;color:#222}
.header-sep{left:855px;top:40px;width:1px;height:38px;background:#ddd}

.hero{left:0;top:110px;width:1200px;height:652px;background:linear-gradient(180deg,#6a6c68 0%,#5b6650 45%,#3e4a35 70%,#2c2c2c 100%)}
.hero-title{left:100px;top:270px;font-family:"Montserrat",sans-serif;font-weight:700;font-size:50px;color:#fff;letter-spacing:.5px}
.hero-sub{left:100px;top:350px;font-style:italic;font-weight:500;font-size:17px;line-height:32px;color:#fff}
.hero-name{left:100px;top:470px;display:flex;align-items:center;gap:12px;font-family:"Montserrat",sans-serif;font-weight:700;font-size:26px;line-height:30px;color:#fff}
.hero-square{width:40px;height:40px;background:var(--red)}
.dots{left:652px;top:516px;display:flex;gap:6px}
.dots span{width:10px;height:10px;border-radius:50%;background:#fff}
.dots span:first-child{background:var(--red)}
.hero-cut{left:0;top:560px}

.choose-title{left:0;top:772px;width:1200px;text-align:center;font-family:"Montserrat",sans-serif;font-weight:700;font-size:29px;color:var(--ink)}
.choose-sub{left:0;top:820px;width:1200px;text-align:center;font-family:"Montserrat",sans-serif;font-weight:300;font-size:28px;color:var(--red)}
.choose-copy{left:200px;top:882px;width:800px;text-align:center;font-size:13px;line-height:27px;color:var(--light)}
.btn{position:absolute;top:973px;height:54px;border-radius:27px;display:flex;align-items:center;justify-content:center;font-weight:700;font-size:14px;text-transform:uppercase}
.btn-solid{background:var(--red);color:#fff}
.btn-line{border:2px solid var(--navy);color:var(--navy)}

.packages{left:0;top:1135px;width:1200px;height:707px;background:var(--navy)}
.packages-title{left:0;top:1238px;width:1200px;text-align:center;font-family:"Montserrat",sans-serif;font-weight:600;font-size:29px;color:#fff}
.arrow{position:absolute;top:1512px;width:38px;height:38px;border:2px solid #fff;border-radius:50%;display:flex;align-items:center;justify-content:center}
.card{position:absolute;top:1331px;width:240px;height:399px;background:#fff;border-radius:3px;overflow:hidden}
.card-head{height:61px;background:var(--card-head);display:flex;justify-content:space-between;align-items:center;padding:0 26px}
.card-name{font-family:"Montserrat",sans-serif;font-weight:700;font-size:18px;color:var(--navy)}
.card-price{font-weight:700;font-size:16px;color:var(--red)}
.card-list{list-style:none;padding:0 10px}
.card-list li{position:relative;padding:16px 6px 14px 32px;font-size:13px;line-height:23px;color:#444;border-bottom:1px solid #e6e6e6}
.card-list li svg{position:absolute;left:6px;top:21px}
.card-buy{position:absolute;left:62px;top:341px;width:116px;height:39px;border-radius:20px;background:var(--red);color:#fff;font-weight:700;font-size:14px;display:flex;align-items:center;justify-content:center}

.subscribe{left:0;top:1842px;width:1200px;height:745px;background:var(--mist)}
.sub-title{left:0;top:1925px;width:1200px;text-align:center;font-family:"Montserrat",sans-serif;font-weight:600;font-size:26px;line-height:44px;color:var(--ink)}
.rule{position:absolute;left:257px;width:686px;height:1px;background:#d9d6d6}
.feature-icon{position:absolute;width:80px;height:80px;border:2px solid var(--navy);border-radius:50%;display:flex;align-items:center;justify-content:center}
.feature-text{position:absolute;width:320px;font-size:15px;line-height:24.5px;color:#555}
.feature-text em{font-style:normal;color:var(--red)}
.field{position:absolute;top:2446px;height:50px;border-radius:25px;background:#fff;border:1px solid #ddd;font-size:14px;color:#999;display:flex;align-items:center;padding-left:32px}
.sub-btn{left:810px;top:2446px;width:162px;height:50px;border-radius:25px;background:var(--red);color:#fff;font-weight:700;font-size:17px;display:flex;align-items:center;justify-content:center}

.footer{left:0;top:2587px;width:1200px;height:270px;background:var(--footer)}
.social{position:absolute;top:2654px;width:38px;height:38px;border:2px solid #fff;border-radius:50%}
.foot-nav{left:0;top:2726px;width:711px;text-align:center;font-size:16px;color:#fff;word-spacing:2px}
.foot-nav span{margin:0 20px}
.copy{left:0;top:2778px;width:711px;text-align:center;font-size:11px;color:#fff}
.foot-sep{left:711px;top:2600px;width:1px;height:250px;background:#333}
.foot-brand{left:766px;top:2700px;display:flex;align-items:center;gap:14px;font-family:"Montserrat",sans-serif;font-weight:700;font-size:28px;line-height:30px;color:#fff}
.foot-square{width:50px;height:50px;border:4px solid #fff}
</style>
</head>
<body>
<div class="abs top-rule"></div>

<header class="abs header">
  <div class="abs brand"><span class="brand-mark"></span><span>TALLY PORCH<br>HELPERS</span></div>
  <nav class="nav">
    <a style="left:368px">How it works</a>
    <a style="left:495px">Service area</a>
    <a style="left:619px">Pricing</a>
    <a style="left:709px">About us</a>
    <a style="left:812px">Faq</a>
  </nav>
  <div class="abs header-sep"></div>
  <div class="abs phone-circle">
    <svg width="16" height="16" viewBox="0 0 24 24"><path fill="#211e7a" d="M6.6 10.8a15 15 0 0 0 6.6 6.6l2.2-2.2c.3-.3.7-.4 1-.2 1.1.4 2.3.6 3.6.6.6 0 1 .4 1 1V20c0 .6-.4 1-1 1A17 17 0 0 1 3 4c0-.6.4-1 1-1h3.5c.6 0 1 .4 1 1 0 1.3.2 2.5.6 3.6.1.3 0 .7-.2 1z"/></svg>
  </div>
  <div class="abs call">Call Us : 1 555 010 2040</div>
</header>

<section class="abs hero" role="img" aria-label="Photo of a suburban house front with shrubs, lamps and an open house for-sale sign on the lawn"></section>
<h1 class="abs hero-title">TALLY PORCH HELPERS</h1>
<p class="abs hero-sub">Helping agents save time and money. We place signs and boost foot traffic to your<br>open houses using proven marketing techniques.</p>
<div class="abs hero-name"><span class="hero-square"></span><span>TALLY PORCH<br>HELPERS</span></div>
<div class="abs dots"><span></span><span></span><span></span><span></span><span></span></div>
<svg class="abs hero-cut" width="1200" height="203" viewBox="0 0 1200 203">
  <polygon points="0,203 781,34 1200,203 0,203" fill="#fff"/>
  <polygon points="400,110 781,21 972,107 781,34" fill="#211e7a"/>
  <g transform="translate(781,63)" fill="none" stroke="#211e7a" stroke-width="2">
    <path d="M-10,-1 L0,-10 L10,-1 M-7,-3 V9 H7 V-3"/>
    <rect x="-2" y="2" width="4" height="4"/>
  </g>
</svg>

<h2 class="abs choose-title">CHOOSE THE OPTION BELOW THAT</h2>
<p class="abs choose-sub">BEST DESCRIBES YOU</p>
<p class="abs choose-copy">Nemo enim ipsam voluptatem quia voluptas sit aspernatur aut odit aut fugit, sed quia consequuntur magni dolores eos qui ratione<br>voluptatem sequi nesciunted quia non numquam eius modi temre magnam aliquam quaerat voluptatem</p>
<div class="btn btn-solid" style="left:204px;width:238px">I'm a full on brokerage</div>
<div class="btn btn-line" style="left:455px;width:273px">I'm an ind. broker with a team</div>
<div class="btn btn-line" style="left:741px;width:255px">I need sign placement asap</div>

<section class="abs packages"></section>
<h2 class="abs packages-title">OUR PACKAGES</h2>
<div class="arrow" style="left:34px"><svg width="14" height="14" viewBox="0 0 14 14"><path d="M9 2 L4 7 L9 12" fill="none" stroke="#fff" stroke-width="2.5"/></svg></div>
<div class="arrow" style="left:1128px"><svg width="14" height="14" viewBox="0 0 14 14"><path d="M5 2 L10 7 L5 12" fill="none" stroke="#fff" stroke-width="2.5"/></svg></div>

<article class="card" style="left:99px">
  <div class="card-head"><span class="card-name">5 SIGNS</span><span class="card-price">$79.9</span></div>
  <ul class="card-list">
    <li><svg width="12" height="12" viewBox="0 0 12 12"><path d="M1 6 L4.5 9.5 L11 2" fill="none" stroke="#e3051b" stroke-width="2.4"/></svg>Place signs strategically in best areas according to where the open house is located</li>
    <li><svg width="12" height="12" viewBox="0 0 12 12"><path d="M1 6 L4.5 9.5 L11 2" fill="none" stroke="#e3051b" stroke-width="2.4"/></svg>Pick Up the signs after the open house</li>
    <li style="border:0"><svg width="12" height="12" viewBox="0 0 12 12"><path d="M1 6 L4.5 9.5 L11 2" fill="none" stroke="#e3051b" stroke-width="2.4"/></svg>Store custom signs for you if needed</li>
  </ul>
  <div class="card-buy">BUY NOW</div>
</article>
<article class="card" style="left:354px">
  <div class="card-head"><span class="card-name">10 SIGNS</span><span class="card-price">$79.9</span></div>
  <ul class="card-list">
    <li><svg width="12" height="12" viewBox="0 0 12 12"><path d="M1 6 L4.5 9.5 L11 2" fill="none" stroke="#e3051b" stroke-width="2.4"/></svg>Place signs strategically in best areas according to where the open house is located</li>
    <li><svg width="12" height="12" viewBox="0 0 12 12"><path d="M1 6 L4.5 9.5 L11 2" fill="none" stroke="#e3051b" stroke-width="2.4"/></svg>Pick Up the signs after the open house</li>
    <li style="border:0"><svg width="12" height="12" viewBox="0 0 12 12"><path d="M1 6 L4.5 9.5 L11 2" fill="none" stroke="#e3051b" stroke-width="2.4"/></svg>Store custom signs for you if needed</li>
  </ul>
  <div class="card-buy">BUY NOW</div>
</article>
<article class="card" style="left:608px">
  <div class="card-head"><span class="card-name">15 SIGNS</span><span class="card-price">$79.9</span></div>
  <ul class="card-list">
    <li><svg width="12" height="12" viewBox="0 0 12 12"><path d="M1 6 L4.5 9.5 L11 2" fill="none" stroke="#e3051b" stroke-width="2.4"/></svg>Place signs strategically in best areas according to where the open house is located</li>
    <li><svg width="12" height="12" viewBox="0 0 12 12"><path d="M1 6 L4.5 9.5 L11 2" fill="none" stroke="#e3051b" stroke-width="2.4"/></svg>Pick Up the signs after the open house</li>
    <li style="border:0"><svg width="12" height="12" viewBox="0 0 12 12"><path d="M1 6 L4.5 9.5 L11 2" fill="none" stroke="#e3051b" stroke-width="2.4"/></svg>Store custom signs for you if needed</li>
  </ul>
  <div class="card-buy">BUY NOW</div>
</article>
<article class="card" style="left:863px">
  <div class="card-head"><span class="card-name">20 SIGNS</span><span class="card-price">$79.9</span></div>
  <ul class="card-list">
    <li><svg width="12" height="12" viewBox="0 0 12 12"><path d="M1 6 L4.5 9.5 L11 2" fill="none" stroke="#e3051b" stroke-width="2.4"/></svg>Place signs strategically in best areas according to where the open house is located</li>
    <li><svg width="12" height="12" viewBox="0 0 12 12"><path d="M1 6 L4.5 9.5 L11 2" fill="none" stroke="#e3051b" stroke-width="2.4"/></svg>Pick Up the signs after the open house</li>
    <li style="border:0"><svg width="12" height="12" viewBox="0 0 12 12"><path d="M1 6 L4.5 9.5 L11 2" fill="none" stroke="#e3051b" stroke-width="2.4"/></svg>Store custom signs for you if needed</li>
  </ul>
  <div class="card-buy">BUY NOW</div>
</article>

<section class="abs subscribe"></section>
<h2 class="abs sub-title">SIGN UP FOR A SUBSCRIPTION AND GET THESE<br>MARKETING SERVICES FOR FREE</h2>
<div class="rule" style="top:2057px"></div>

<div class="feature-icon" style="left:149px;top:2115px">
  <svg width="34" height="40" viewBox="0 0 34 40" fill="none" stroke="#e3051b" stroke-width="2"><rect x="6" y="3" width="18" height="34" rx="3"/><line x1="12" y1="33" x2="18" y2="33"/><rect x="14" y="9" width="17" height="10" fill="#fff"/><text x="22.5" y="17" font-size="6" font-family="Roboto,sans-serif" fill="#e3051b" stroke="none" text-anchor="middle">SMS</text></svg>
</div>
<p class="feature-text" style="left:248px;top:2118px">Send <em>SMS</em> blast to your neighborhood informing them your home is for sale and if they know anyone looking to send them over</p>

<div class="feature-icon" style="left:650px;top:2115px">
  <svg width="40" height="36" viewBox="0 0 40 36" fill="none" stroke="#e3051b" stroke-width="2"><path d="M4 14 L20 3 L36 14 V33 H4 Z"/><path d="M4 14 L20 25 L36 14"/><path d="M4 33 L16 22 M36 33 L24 22"/><rect x="10" y="8" width="20" height="12" fill="#fff"/></svg>
</div>
<p class="feature-text" style="left:747px;top:2118px"><em>Email</em> blast to your neighborhood informing them your home is for sale and if they know anyone looking to send them over</p>

<div class="feature-icon" style="left:149px;top:2246px">
  <svg width="40" height="36" viewBox="0 0 40 36" fill="none" stroke="#e3051b" stroke-width="2.4"><rect x="4" y="10" width="32" height="22" rx="2"/><rect x="9" y="14" width="22" height="14"/><path d="M14 3 L20 10 L26 3"/></svg>
</div>
<p class="feature-text" style="left:248px;top:2274px"><em>Newsfeed</em> ads to people in your open house area</p>

<div class="feature-icon" style="left:650px;top:2246px">
  <svg width="34" height="40" viewBox="0 0 34 40" fill="none" stroke="#e3051b" stroke-width="2"><path d="M6 3 H22 L29 10 V37 H6 Z"/><path d="M22 3 V10 H29"/><rect x="11" y="19" width="14" height="10"/><path d="M16 22 L21 24 L16 26 Z" fill="#e3051b"/></svg>
</div>
<p class="feature-text" style="left:747px;top:2249px"><em>VB blast</em> to your neighborhood informing them your home is for sale and if they know anyone looking to send them over</p>

<div class="rule" style="top:2381px"></div>
<div class="field" style="left:227px;width:274px">Enter Name</div>
<div class="field" style="left:518px;width:275px">Enter Email</div>
<div class="abs sub-btn">SUBSCRIBE</div>

<footer class="abs footer"></footer>
<div class="social" style="left:410px" aria-label="Social profile"></div>
<div class="social" style="left:459px" aria-label="Social profile"></div>
<div class="social" style="left:509px" aria-label="Social profile"></div>
<div class="social" style="left:558px" aria-label="Social profile"></div>
<div class="social" style="left:608px" aria-label="Social profile"></div>
<p class="abs foot-nav">How it works<span>/</span>service<span>/</span>Pricing<span>/</span>About us<span>/</span>Faq</p>
<p class="abs copy">Copyright © 2018, TALLY PORCH HELPERS All Rights Reserved.</p>
<div class="abs foot-sep"></div>
<div class="abs foot-brand"><span class="foot-square"></span><span>TALLY PORCH<br>HELPERS</span></div>
</body>
</html>
```